iPhone iOS 7 App For Managing Tasks/Photos for Internal Company Use

We need an app design that displays company objectives and task, and provides the interface for employees to complete a task by uploading a photo and adding comments.

Please see attached mock up sketches as a rough guideline

Final delivery of files must contain PSD, and all layers/objects sliced both is PSD and PNG files

Target Market(s)

This is a tool for internal employee use

Industry/Entity Type

It Company

Requirements
Must have
• Must include logo, and match the colour scheme
Use iPhone iOS 7 Style

```html
<!DOCTYPE html>
<html lang="en">
<head>
<meta charset="utf-8">
<title>Objectives</title>
<link rel="stylesheet" href="https://fonts.googleapis.com/css2?family=Inter:wght@400;500;600&display=swap">
<style>
  :root {
    --bg-page: #f4f4f4;
    --bg-surface: #ffffff;
    --line: #dcdcdc;
    --text-main: #111111;
    --progress-start: #ffffff;
    --progress-end: #e4e9ee;
    --chevron: #a9b4bc;
    --tabbar: #3d5f63;
    --tab-icon: #e3ecec;
    --badge: #e8412f;
  }
  * { margin: 0; padding: 0; box-sizing: border-box; }
  html, body { width: 677px; height: 1200px; overflow: hidden; }
  body {
    position: relative;
    background: var(--bg-page);
    font-family: "Inter", "Helvetica Neue", Arial, sans-serif;
    color: var(--text-main);
  }
  .status-bar {
    position: absolute; top: 0; left: 0; width: 677px; height: 45px;
    background: var(--bg-surface);
    display: flex; align-items: center; justify-content: space-between;
    padding: 0 14px; font-size: 25px; font-weight: 500;
  }
  .status-left, .status-right { display: flex; align-items: center; gap: 8px; }
  .status-time { position: absolute; left: 0; right: 0; text-align: center; font-weight: 600; pointer-events: none; }
  .nav-bar {
    position: absolute; top: 45px; left: 0; width: 677px; height: 91px;
    background: var(--bg-surface);
    border-bottom: 2px solid var(--line);
    display: flex; align-items: center; justify-content: center;
  }
  .nav-title { font-size: 38px; font-weight: 600; margin-top: -5px; }
  .task-row {
    position: absolute; left: 0; width: 677px; height: 92px;
    background: var(--bg-surface);
    border-top: 2px solid var(--line);
    border-bottom: 2px solid var(--line);
  }
  .task-progress {
    position: absolute; top: 0; left: 0; bottom: 0;
    background: linear-gradient(to right, var(--progress-start) 20%, var(--progress-end));
  }
  .task-name {
    position: absolute; left: 27px; top: 0; bottom: 0;
    display: flex; align-items: center; font-size: 32px;
  }
  .task-chevron { position: absolute; right: 18px; top: 32px; }
  .tab-bar {
    position: absolute; left: 0; bottom: 0; width: 677px; height: 108px;
    background: var(--tabbar);
  }
  .tab-icon { position: absolute; top: 32px; }
</style>
</head>
<body>
  <header class="status-bar">
    <div class="status-left">
      <svg width="64" height="14" viewBox="0 0 64 14">
        <circle cx="6" cy="7" r="5.5" fill="#111"/>
        <circle cx="19" cy="7" r="5.5" fill="#111"/>
        <circle cx="32" cy="7" r="5.5" fill="#111"/>
        <circle cx="45" cy="7" r="5" fill="none" stroke="#111" stroke-width="1.3"/>
        <circle cx="58" cy="7" r="5" fill="none" stroke="#111" stroke-width="1.3"/>
      </svg>
      <span>NOVA</span>
      <svg width="26" height="20" viewBox="0 0 26 20">
        <path d="M13 19 L9 14.5 A6 6 0 0 1 17 14.5 Z" fill="#111"/>
        <path d="M5 10.5 A11.5 11.5 0 0 1 21 10.5" fill="none" stroke="#111" stroke-width="3"/>
        <path d="M1 6 A17 17 0 0 1 25 6" fill="none" stroke="#111" stroke-width="3"/>
      </svg>
    </div>
    <div class="status-time">4:21 PM</div>
    <div class="status-right">
      <svg width="14" height="24" viewBox="0 0 14 24">
        <path d="M2 6 L12 17 L7 22 V2 L12 7 L2 18" fill="none" stroke="#111" stroke-width="1.8"/>
      </svg>
      <span>22%</span>
      <svg width="50" height="22" viewBox="0 0 50 22">
        <rect x="1" y="1" width="43" height="20" rx="3" fill="none" stroke="#111" stroke-width="1.6"/>
        <rect x="4" y="4" width="9" height="14" fill="#111"/>
        <rect x="45" y="7" width="3" height="8" fill="#111"/>
      </svg>
    </div>
  </header>

  <div class="nav-bar"><h1 class="nav-title">Objectives</h1></div>

  <main class="task-list">
    <div class="task-row" style="top:241px">
      <div class="task-progress" style="width:515px"></div>
      <span class="task-name">Task 1</span>
      <svg class="task-chevron" width="16" height="26" viewBox="0 0 16 26"><path d="M3 3 L13 13 L3 23" fill="none" stroke="var(--chevron)" stroke-width="3"/></svg>
    </div>
    <div class="task-row" style="top:368px">
      <div class="task-progress" style="width:232px"></div>
      <span class="task-name">Task 2</span>
      <svg class="task-chevron" width="16" height="26" viewBox="0 0 16 26"><path d="M3 3 L13 13 L3 23" fill="none" stroke="var(--chevron)" stroke-width="3"/></svg>
    </div>
    <div class="task-row" style="top:501px">
      <div class="task-progress" style="width:677px"></div>
      <span class="task-name">Task 3</span>
      <svg class="task-chevron" width="16" height="26" viewBox="0 0 16 26"><path d="M3 3 L13 13 L3 23" fill="none" stroke="var(--chevron)" stroke-width="3"/></svg>
    </div>
    <div class="task-row" style="top:634px">
      <div class="task-progress" style="width:50px"></div>
      <span class="task-name">Task 4</span>
      <svg class="task-chevron" width="16" height="26" viewBox="0 0 16 26"><path d="M3 3 L13 13 L3 23" fill="none" stroke="var(--chevron)" stroke-width="3"/></svg>
    </div>
    <div class="task-row" style="top:767px">
      <div class="task-progress" style="width:320px"></div>
      <span class="task-name">Task 5</span>
      <svg class="task-chevron" width="16" height="26" viewBox="0 0 16 26"><path d="M3 3 L13 13 L3 23" fill="none" stroke="var(--chevron)" stroke-width="3"/></svg>
    </div>
  </main>

  <nav class="tab-bar">
    <svg class="tab-icon" style="left:62px" width="44" height="44" viewBox="0 0 44 44" aria-label="Home">
      <path d="M22 3 L42 22 H36 V41 H26 V29 H18 V41 H8 V22 H2 Z" fill="var(--tab-icon)"/>
    </svg>
    <svg class="tab-icon" style="left:231px" width="44" height="44" viewBox="0 0 44 44" aria-label="Progress">
      <path d="M20 4 A19 19 0 1 0 40 24 H20 Z" fill="var(--tab-icon)"/>
      <path d="M24 0 A19 19 0 0 1 44 20 H24 Z" fill="var(--tab-icon)"/>
    </svg>
    <svg class="tab-icon" style="left:400px" width="50" height="44" viewBox="0 0 50 44" aria-label="Messages">
      <rect x="2" y="8" width="36" height="24" rx="2" fill="var(--tab-icon)"/>
      <path d="M8 31 V42 L20 31 Z" fill="var(--tab-icon)"/>
      <rect x="8" y="14" width="24" height="3" fill="var(--tabbar)"/>
      <rect x="8" y="21" width="24" height="3" fill="var(--tabbar)"/>
      <circle cx="41" cy="8" r="7" fill="var(--badge)"/>
    </svg>
    <svg class="tab-icon" style="left:574px" width="44" height="44" viewBox="0 0 44 44" aria-label="Sign out">
      <path d="M26 14 V4 H3 V40 H26 V30" fill="none" stroke="var(--tab-icon)" stroke-width="5"/>
      <path d="M14 22 H36" stroke="var(--tab-icon)" stroke-width="5"/>
      <path d="M30 13 L41 22 L30 31 Z" fill="var(--tab-icon)"/>
    </svg>
  </nav>
</body>
</html>
```